Oil and Gas Exploration and Production company needs a business card design

We need a business card design using our logo and colors in the logo. We want a mainstream design.

```html
<!DOCTYPE html>
<html lang="en">
<head>
<meta charset="utf-8">
<title>Solano Oil &amp; Gas — Business Card</title>
<link rel="stylesheet" href="https://fonts.googleapis.com/css2?family=Work+Sans:wght@400;500;600&display=swap">
<style>
  :root {
    --backdrop: #2b2b2b;
    --card: #1c1c1c;
    --card-edge: #262626;
    --gold: #d29a22;
    --white: #f4f4f4;
    --muted: #e6e6e6;
  }
  * { margin: 0; padding: 0; box-sizing: border-box; }
  html, body {
    width: 1200px; height: 900px; overflow: hidden;
    background: var(--backdrop);
    font-family: "Work Sans", Arial, sans-serif;
  }
  .sheet {
    width: 1200px; height: 900px;
    display: flex; flex-direction: column;
    align-items: center; justify-content: center; gap: 40px;
  }
  .card {
    width: 700px; height: 400px;
    background: linear-gradient(135deg, var(--card) 0%, var(--card-edge) 100%);
    position: relative;
  }
  /* Front */
  .card--front { display: flex; align-items: center; justify-content: center; }
  .brand { display: flex; align-items: center; gap: 18px; }
  .brand__dot { width: 44px; height: 44px; border-radius: 50%; background: var(--gold); }
  .brand__name {
    color: var(--white); font-weight: 600; font-size: 46px; letter-spacing: 0.5px;
  }
  /* Back */
  .card--back { color: var(--muted); }
  .identity {
    position: absolute; left: 150px; top: 130px; width: 210px; text-align: right;
  }
  .identity__name { color: var(--gold); font-size: 32px; font-weight: 500; line-height: 1.1; white-space: nowrap; }
  .identity__title { font-size: 17px; margin-top: 6px; letter-spacing: 1px; }
  .divider {
    position: absolute; left: 385px; top: 132px; width: 3px; height: 62px; background: var(--gold);
  }
  .contacts {
    position: absolute; left: 410px; top: 132px; list-style: none;
    font-size: 17px; line-height: 22px;
  }
  .contacts li { display: flex; align-items: center; gap: 10px; }
  .contacts svg { width: 13px; height: 13px; flex: none; }
  .contacts .accent { color: var(--gold); }
  .address {
    position: absolute; left: 150px; bottom: 70px; font-size: 19px; letter-spacing: 0.5px;
  }
</style>
</head>
<body>
<main class="sheet">
  <section class="card card--front" aria-label="Card front">
    <div class="brand">
      <span class="brand__dot" aria-hidden="true"></span>
      <span class="brand__name">Solano Oil &amp; Gas</span>
    </div>
  </section>

  <section class="card card--back" aria-label="Card back">
    <div class="identity">
      <p class="identity__name">Dana Whitford</p>
      <p class="identity__title">CFO</p>
    </div>
    <span class="divider" aria-hidden="true"></span>
    <ul class="contacts">
      <li>
        <svg viewBox="0 0 16 16" aria-hidden="true"><path d="M4 1l3 3-2 2c1 2 3 4 5 5l2-2 3 3-2 3C7 15 1 9 1 3z" fill="none" stroke="var(--gold)" stroke-width="1.6"/></svg>
        (555) 014-2278
      </li>
      <li>
        <svg viewBox="0 0 16 16" aria-hidden="true"><rect x="1" y="3" width="14" height="10" fill="none" stroke="var(--gold)" stroke-width="1.6"/><path d="M1 3l7 6 7-6" fill="none" stroke="var(--gold)" stroke-width="1.6"/></svg>
        info@solanoenergy.com
      </li>
      <li>
        <svg viewBox="0 0 16 16" aria-hidden="true"><circle cx="8" cy="8" r="6.5" fill="none" stroke="var(--gold)" stroke-width="1.5"/><ellipse cx="8" cy="8" rx="3" ry="6.5" fill="none" stroke="var(--gold)" stroke-width="1.2"/><path d="M1.5 8h13" stroke="var(--gold)" stroke-width="1.2"/></svg>
        <span>www.<span class="accent">solanoenergy</span>.com</span>
      </li>
    </ul>
    <p class="address">2450 Meridian Ave, Cedar Falls, Texas us</p>
  </section>
</main>
</body>
</html>
```